Health Wellbeing Beauty online Shop

I have attached a full spec, however in summary this is a new business startup selling skincare products.

We need a web design for new wellbeing website, selling skincare products so need an eCommerce solution . On the home page I would like these faces to dissolve into each other on a loop or use a honeycomb style transation.
You will need the option of being able to log into an account, either through lumigram, vexora, chirplo or create an account. For created accounts, obviously need the facility to be able to reset passwords, see previous orders, track current order, and maintain favourites.
It should be PC, mobile and tablet friendly.

Look and Feel
It should be an elegant, modern, professional, trendy, unisex website. It should look clean and calm. Am happy to try interesting and slightly unusual designs. I would also like to have chat functionality, either powered by talvuNchat or by Quo 58.
Websites I like are
https://www.nobel-radiance.example.co.uk/
https://www.mereminerals.example.co.uk/
http://www.brightdermis.example.com/

PLEASE DO USE YOUR KNOWELDGE OF WHAT WORKS FOR WEB DESIGN. YOU’RE THE EXPERT AND NEED YOUR EXPERTISE. CARTE BLANCHE TO DESIGN AS YOU SEE FIT. Please be creative, I need my site to stand out from the crowd.

Target Market(s)

Target Market
Middle aged women are our most common client, however, younger patients, both male and female, will often visit the site. In summary, I would like the site to appeal to all age brackets.

Industry/Entity Type

Business

Coding

Coded - Design and coding required

Number of Pages Required

4 page

Requirements
Must have
• Need shop to be exactly like shop on this link http://www.brightdermis.example.com/
Nice to have
• i would like something unique and creative

```html
<!DOCTYPE html>
<html lang="en">
<head>
<meta charset="utf-8">
<title>Aurelle – Skin Lightening Tablets</title>
<link rel="stylesheet" href="https://fonts.googleapis.com/css2?family=Lora:wght@400;700&family=Open+Sans:wght@400;600;700&display=swap">
<style>
:root{
  --ink:#222;
  --header:#1e1e1e;
  --gold:#f3c13c;
  --gold-text:#e6b93a;
  --chirplo:#2d9bd9;
  --lumigram:#3a5a9b;
  --panel:#2b2b2b;
  --footer-left:#343434;
  --footer-right:#2c2c2c;
  --bottom:#1c1c1c;
  --line:#d6d6d6;
  --muted:#6d6d6d;
  --white:#fff;
}
*{box-sizing:border-box;margin:0;padding:0}
html,body{width:1200px;height:2311px;overflow:hidden;background:var(--white);font-family:"Open Sans",sans-serif;color:var(--ink)}
.page{position:relative;width:1200px;height:2311px}
.abs{position:absolute}

/* header */
.site-header{left:132px;top:9px;width:936px;height:196px;background:var(--header)}
.brand{left:18px;top:56px;font-family:"Lora",serif;font-size:30px;font-weight:400;color:var(--gold-text)}
.btn{position:absolute;top:23px;height:39px;display:flex;align-items:center;justify-content:center;font-size:12px;font-weight:600;color:var(--white);border-radius:2px}
.btn-chirplo{left:446px;width:146px;background:var(--chirplo)}
.btn-lumigram{left:600px;width:171px;background:var(--lumigram)}
.btn-account{left:777px;width:148px;background:var(--gold);color:#2a2a2a}
.social{position:absolute;top:93px;width:27px;height:27px;border-radius:50%}
.social-lumigram{left:515px;background:var(--lumigram)}
.social-chirplo{left:545px;background:var(--chirplo)}
.cart{left:590px;top:92px;color:var(--white);text-align:right;width:90px}
.cart small{display:block;font-size:10px}
.cart strong{font-size:14px;font-weight:400}
.cart-icon{left:688px;top:96px}
.search{left:709px;top:90px;width:216px;height:38px;background:var(--white);display:flex;align-items:center;justify-content:space-between;padding:0 12px;font-size:12px;color:#555}
.main-nav{left:7px;top:151px;width:921px;height:42px;background:var(--white);font-family:"Lora",serif;font-size:12.5px}
.main-nav a{color:var(--ink);text-decoration:none;position:absolute;top:0;height:42px;line-height:42px}
.main-nav a.active{background:var(--gold);left:0;width:181px;text-align:center}

/* hero */
.hero{left:132px;top:211px;width:936px;height:402px;background:linear-gradient(100deg,#c89a7a 0%,#e6c5ad 25%,#8a6a55 50%,#dcb79b 72%,#b88d70 100%)}

/* sidebar */
.side-title{font-family:"Lora",serif;font-size:27px;font-weight:400;color:var(--ink);left:132px}
.filter{left:132px;width:201px;background:var(--panel);padding:0 8px 8px}
.filter-head{color:var(--white);font-size:12px;height:36px;line-height:36px;padding-left:8px}
.filter ul{list-style:none;background:var(--white);padding:10px 0 4px 14px}
.filter li{font-size:12px;height:32px;line-height:28px;color:#333}
.filter li::before,.cat li::before{content:"›";margin-right:10px}
.cat{left:132px;width:201px;list-style:none}
.cat li{height:37px;line-height:37px;border:1px solid var(--line);margin-bottom:3px;font-size:12px;padding-left:10px}
.cat li::before{content:"»"}
.cat li.active{background:var(--panel);color:var(--white);border-color:var(--panel)}
.ad{left:132px;top:1360px;width:201px;height:239px;border:2px solid var(--panel);background:linear-gradient(180deg,#f4f4f4 0%,#f4f4f4 55%,#a9d4de 62%,#a8c77a 100%)}

/* shop */
.shop-title{left:371px;top:640px;font-family:"Lora",serif;font-size:27px;font-weight:400}
.sort{left:884px;top:645px;font-size:11px;display:flex;align-items:center;gap:6px}
.sort span.box{border:1px solid #ccc;padding:6px 8px;width:136px;font-size:10.5px}
.grid{left:373px;top:692px;width:694px;display:grid;grid-template-columns:repeat(3,223px);column-gap:12px;row-gap:14px}
.card{height:371px;border:1px solid var(--line);text-align:center;padding-top:22px}
.product-photo{width:160px;height:182px;margin:0 auto;background:radial-gradient(ellipse at center,#d08a4a 0%,#e9d6c6 60%,#f6f2ee 100%)}
.card h3{font-family:"Lora",serif;font-weight:400;font-size:15px;line-height:21px;margin:16px 14px 0;color:#222}
.price{font-family:"Lora",serif;font-size:16px;color:#555;margin-top:4px}
.price small{font-size:11px}
.stars{margin-top:4px;height:18px}
.actions{display:flex;justify-content:center;gap:22px;font-size:12px;color:#555;margin-top:8px;align-items:center}
.actions span{display:flex;align-items:center;gap:6px}
.pager{left:607px;top:1869px;display:flex;gap:6px}
.pager span{width:27px;height:27px;border-radius:50%;background:#e4e4e4;font-size:10px;color:#666;display:flex;align-items:center;justify-content:center}
.pager span.current{background:var(--gold);color:#333}

/* footer */
.footer{left:0;top:1935px;width:1200px;height:280px;display:flex}
.footer-about{width:599px;background:var(--footer-left);padding:28px 0 0 132px;color:#aaa}
.footer-contact{width:601px;background:var(--footer-right);padding:28px 0 0 46px;color:#ccc}
.footer h2{font-family:"Lora",serif;font-weight:400;font-size:27px;color:var(--gold-text);margin-bottom:10px}
.footer p{font-size:10.5px;line-height:17.5px}
.footer-about p{width:440px}
.footer .strong{color:var(--white);font-size:12px;line-height:20px}
.footer .ghost{display:inline-block;border:1px solid #888;color:#ccc;font-size:11px;padding:10px 14px;margin-top:12px}
.bottom-bar{left:0;top:2215px;width:1200px;height:96px;background:var(--bottom);color:#aaa;font-size:10.5px}
.bottom-links{position:absolute;left:132px;top:24px;word-spacing:2px}
.copy{position:absolute;left:132px;top:54px}
.cards{position:absolute;left:908px;top:36px;display:flex;gap:5px}
.cards span{height:21px;padding:0 5px;background:var(--white);color:#234;font-size:8px;line-height:21px;border-radius:2px}
.chat{position:absolute;left:678px;top:53px;width:228px;height:43px;background:var(--gold);color:#333;font-size:14px;display:flex;align-items:center;justify-content:center;gap:10px}
.chat small{font-size:8px}
</style>
</head>
<body>
<svg width="0" height="0" style="position:absolute">
  <symbol id="star" viewBox="0 0 24 24"><path d="M12 2l3 6.6 7.2.7-5.4 4.8 1.6 7.1L12 17.5 5.6 21.2l1.6-7.1L1.8 9.3 9 8.6z" fill="#f0b51e"/></symbol>
  <symbol id="eye" viewBox="0 0 24 24"><path d="M1 12s4-7 11-7 11 7 11 7-4 7-11 7S1 12 1 12z" fill="#555"/><circle cx="12" cy="12" r="3.5" fill="#fff"/></symbol>
  <symbol id="cart" viewBox="0 0 24 24"><path d="M1 3h4l3 11h12l3-8H7" fill="none" stroke="#555" stroke-width="2.4"/><circle cx="9" cy="19" r="2" fill="#555"/><circle cx="18" cy="19" r="2" fill="#555"/></symbol>
  <symbol id="stars5" viewBox="0 0 100 18"><use href="#star" x="0" width="18" height="18"/><use href="#star" x="20" width="18" height="18"/><use href="#star" x="40" width="18" height="18"/><use href="#star" x="60" width="18" height="18"/><use href="#star" x="80" width="18" height="18"/></symbol>
</svg>
<div class="page">

<header class="site-header abs">
  <div class="brand abs">Aurelle</div>
  <a class="btn btn-chirplo">Login with chirplo</a>
  <a class="btn btn-lumigram">Login with lumigram</a>
  <a class="btn btn-account">✎&nbsp; Create An Account</a>
  <span class="social social-lumigram" aria-label="lumigram"></span>
  <span class="social social-chirplo" aria-label="chirplo"></span>
  <div class="cart abs"><small>My Cart</small><strong>$00.00</strong></div>
  <svg class="cart-icon abs" width="36" height="32" viewBox="0 0 36 32">
    <rect x="2" y="9" width="30" height="20" fill="none" stroke="#fff" stroke-width="2"/>
    <path d="M2 16h30M2 22h30M10 9v20M17 9v20M24 9v20" stroke="#fff" stroke-width="1.5"/>
    <circle cx="6" cy="6" r="6" fill="#f3c13c"/><text x="6" y="9" font-size="8" text-anchor="middle" fill="#222" font-family="Open Sans,sans-serif">0</text>
  </svg>
  <div class="search abs"><span>Search</span>
    <svg width="14" height="14" viewBox="0 0 14 14"><circle cx="6" cy="6" r="4.5" fill="none" stroke="#333" stroke-width="2"/><path d="M9.5 9.5L13 13" stroke="#333" stroke-width="2"/></svg>
  </div>
  <nav class="main-nav abs">
    <a class="active">Skin Lightening Tablets</a>
    <a style="left:212px">Skin Lightening Creams</a>
    <a style="left:398px">Skin Lightening Soaps</a>
    <a style="left:574px">Skin Lightening Vials</a>
    <a style="left:745px">Contact</a>
    <a style="left:850px">About Us</a>
  </nav>
</header>

<div class="hero abs" role="img" aria-label="Honeycomb mosaic of faces of different ages and backgrounds"></div>

<h2 class="side-title abs" style="top:640px">Refine by</h2>
<div class="filter abs" style="top:682px">
  <div class="filter-head">» &nbsp;Price Range</div>
  <ul><li>Highest review score</li><li>Price high to low</li><li>Price low to high</li></ul>
</div>
<h2 class="side-title abs" style="top:864px">Brand</h2>
<div class="filter abs" style="top:906px">
  <div class="filter-head">» &nbsp;Brand name</div>
  <ul><li>Aenean et bibendum</li><li>Donec sagitti</li><li>Cras suscipit est</li></ul>
</div>
<h2 class="side-title abs" style="top:1088px">Categories</h2>
<ul class="cat abs" style="top:1129px">
  <li class="active">Skin Lightening Tablets</li>
  <li>Skin Lightening Creams</li>
  <li>Skin Lightening Soaps</li>
  <li>Skin Lightening Vials</li>
  <li>Skin Lightening Systems</li>
</ul>
<div class="ad abs" role="img" aria-label="Event promotion banner with skyline illustration"></div>

<h1 class="shop-title abs">Shop</h1>
<div class="sort abs"><span>Sort by :</span><span class="box">Highest review score &nbsp;▾</span></div>

<div class="grid abs">
  <article class="card"><div class="product-photo" role="img" aria-label="Product photo: amber bottle of tablets"></div><h3>Cum sociis natoque penati bus et magnis dis parturi ent montes</h3><p class="price">$00.00<small>/per bottle</small></p><svg class="stars" width="100" height="18"><use href="#stars5"/></svg><div class="actions"><span><svg width="16" height="16"><use href="#eye"/></svg>Quick View</span><span><svg width="16" height="16"><use href="#cart"/></svg>Buy Now</span></div></article>
  <article class="card"><div class="product-photo" role="img" aria-label="Product photo: amber bottle of tablets"></div><h3>Cum sociis natoque penati bus et magnis dis parturi ent montes</h3><p class="price">$00.00<small>/per bottle</small></p><svg class="stars" width="100" height="18"><use href="#stars5"/></svg><div class="actions"><span><svg width="16" height="16"><use href="#eye"/></svg>Quick View</span><span><svg width="16" height="16"><use href="#cart"/></svg>Buy Now</span></div></article>
  <article class="card"><div class="product-photo" role="img" aria-label="Product photo: amber bottle of tablets"></div><h3>Cum sociis natoque penati bus et magnis dis parturi ent montes</h3><p class="price">$00.00<small>/per bottle</small></p><svg class="stars" width="100" height="18"><use href="#stars5"/></svg><div class="actions"><span><svg width="16" height="16"><use href="#eye"/></svg>Quick View</span><span><svg width="16" height="16"><use href="#cart"/></svg>Buy Now</span></div></article>
  <article class="card"><div class="product-photo" role="img" aria-label="Product photo: amber bottle of tablets"></div><h3>Cum sociis natoque penati bus et magnis dis parturi ent montes</h3><p class="price">$00.00<small>/per bottle</small></p><svg class="stars" width="100" height="18"><use href="#stars5"/></svg><div class="actions"><span><svg width="16" height="16"><use href="#eye"/></svg>Quick View</span><span><svg width="16" height="16"><use href="#cart"/></svg>Buy Now</span></div></article>
  <article class="card"><div class="product-photo" role="img" aria-label="Product photo: amber bottle of tablets"></div><h3>Cum sociis natoque penati bus et magnis dis parturi ent montes</h3><p class="price">$00.00<small>/per bottle</small></p><svg class="stars" width="100" height="18"><use href="#stars5"/></svg><div class="actions"><span><svg width="16" height="16"><use href="#eye"/></svg>Quick View</span><span><svg width="16" height="16"><use href="#cart"/></svg>Buy Now</span></div></article>
  <article class="card"><div class="product-photo" role="img" aria-label="Product photo: amber bottle of tablets"></div><h3>Cum sociis natoque penati bus et magnis dis parturi ent montes</h3><p class="price">$00.00<small>/per bottle</small></p><svg class="stars" width="100" height="18"><use href="#stars5"/></svg><div class="actions"><span><svg width="16" height="16"><use href="#eye"/></svg>Quick View</span><span><svg width="16" height="16"><use href="#cart"/></svg>Buy Now</span></div></article>
  <article class="card"><div class="product-photo" role="img" aria-label="Product photo: amber bottle of tablets"></div><h3>Cum sociis natoque penati bus et magnis dis parturi ent montes</h3><p class="price">$00.00<small>/per bottle</small></p><svg class="stars" width="100" height="18"><use href="#stars5"/></svg><div class="actions"><span><svg width="16" height="16"><use href="#eye"/></svg>Quick View</span><span><svg width="16" height="16"><use href="#cart"/></svg>Buy Now</span></div></article>
  <article class="card"><div class="product-photo" role="img" aria-label="Product photo: amber bottle of tablets"></div><h3>Cum sociis natoque penati bus et magnis dis parturi ent montes</h3><p class="price">$00.00<small>/per bottle</small></p><svg class="stars" width="100" height="18"><use href="#stars5"/></svg><div class="actions"><span><svg width="16" height="16"><use href="#eye"/></svg>Quick View</span><span><svg width="16" height="16"><use href="#cart"/></svg>Buy Now</span></div></article>
  <article class="card"><div class="product-photo" role="img" aria-label="Product photo: amber bottle of tablets"></div><h3>Cum sociis natoque penati bus et magnis dis parturi ent montes</h3><p class="price">$00.00<small>/per bottle</small></p><svg class="stars" width="100" height="18"><use href="#stars5"/></svg><div class="actions"><span><svg width="16" height="16"><use href="#eye"/></svg>Quick View</span><span><svg width="16" height="16"><use href="#cart"/></svg>Buy Now</span></div></article>
</div>

<nav class="pager abs"><span>«</span><span class="current">1</span><span>2</span><span>3</span><span>4</span><span>5</span><span>»</span></nav>

<footer class="footer abs">
  <section class="footer-about">
    <h2>About</h2>
    <p>Phasellus non sodales ipsum. Pellentesque ac nisi eu sem suscipit luctus. Duis commodo aliquam mi, non pellentesque est finibus vitae. Maecenas ut faucibus magna, eget volutpat lorem. Nunc vestibulum ut nunc ut tincidunt. Curabitur non ante porttitor lectus volutpat imperdiet interdum sit amet erat. Maecenas convallis erat massa, sit amet faucibus purus imperdiet sed. Sed tellus odio, ullamcorper sed elit consequat, pretium dictum dui. Morbi a euismod sapien, ac porttitor sem. Suspendisse molestie at urna quis accumsan. Suspendisse potenti. Integer id dui elementum, feugiat erat quis.</p>
    <span class="ghost">Read more</span>
  </section>
  <section class="footer-contact">
    <h2>Contact</h2>
    <p>Get in touch for expert confidential supplement advice, or for customer services.</p>
    <p class="strong">Calling from the UK - 0800 555 0142</p>
    <p class="strong">Calling from Overseas - +44 800 555 0142</p>
    <p style="margin-top:6px">To contact us by email, please click the send us a message tab on the right.</p>
    <p class="strong">Our team is available &nbsp;- Monday - Friday: 8am until 18:00pm</p>
    <p>Answerphone out of hours</p>
    <span class="ghost">Quick Contact Us</span>
  </section>
</footer>

<div class="bottom-bar abs">
  <div class="bottom-links">Skin Lightening Tablets &nbsp;| &nbsp;Skin Lightening Creams &nbsp;| &nbsp;Skin Lightening Soaps &nbsp;| &nbsp;Skin Lightening Vials &nbsp;| &nbsp;Contact &nbsp;| &nbsp;About Us</div>
  <div class="copy">Copyright © &nbsp;2016 &nbsp;Aurelle. &nbsp;All rights reserved.</div>
  <div class="cards"><span>Paynest</span><span>Discora</span><span>Vanta Volt</span><span>Vanta</span></div>
  <div class="chat">
    <svg width="18" height="16" viewBox="0 0 18 16"><path d="M2 1h14v9H7l-4 4v-4H2z" fill="#333"/></svg>
    Live Chat with us <small>Quo 58</small>
  </div>
</div>

</div>
</body>
</html>
```